Business Cards for IT Consulting Company (Managed Service Provider)

I am looking to have some business cards printed and would like some designs. We are an IT Consulting company based in Vancouver BC. I would like a nice clean and modern look to the cards. I have uploaded all the versions of my logo so parts can be used as needed. Here is a snippit from our website homepage:

Quillbrook Networks Ltd. is an IT Solutions Partner located in Vancouver BC, Canada. We offer IT solutions and support to customers in the greater Vancouver Area. With expertise in Microsoft platforms, as well as Linux and Mac OSX and over 12 years experience in the IT industry, Quillbrook Networks is dedicated to offering our clients top quality service and products. We take pride in the solutions we offer our customers. The greatest compliment a client can give us is to recommend our services.

Quillbrook Networks Ltd. offers a wide range of IT services from onsite service to remote support and managed service solutions. This allows clients to choose the support path that best suits their company’s needs. Supporting many different sized companies from small to enterprise level over the past 12 years Quillbrook Networks has the experience and expertise needed to ensure things run smoothly. Allowing our clients to focus on doing business.

Revolutionizing the way IT services are delivered.

Quillbrook Networks is dedicated to providing our clients with IT solutions that work and grow with them for years to come. This philosophy helps save money in the long run instead of replacing equipment constantly. Far too often IT solutions are not well thought out and while possibly solving the problem at hand, require replacement due to growth or quality within a very short time frame. Quillbrook Networks takes pride in providing solutions that will last and be able to accommodate growth without the need for replacement.

Industry/Entity Type

Information Technology

Contact Information for Business Card

Quillbrook Networks Ltd.
(Employee Name)
Eml: (Employees Email Address)
Web: quillbrook.me
Ph: 604-555-0148

Font styles to use
Serif
Sans Serif

Requirements
Must have
• The Company logo and company colors.
Nice to have
• - Our tag line: "Revolutionizing IT Services" or "Revolutionizing the way IT services are delivered."
• - Also I really like the idea of nature and technology together blending which is sort of where my logo came from so integrating that somehow onto the business cards would be great.

```html
<!DOCTYPE html>
<html lang="en">
<head>
<meta charset="utf-8">
<title>Quillbrook Networks – Business Cards</title>
<link rel="stylesheet" href="https://fonts.googleapis.com/css2?family=Montserrat:wght@500;600&family=Arimo:wght@400;700&display=swap">
<style>
  :root {
    --bg: #e9e7e3;
    --slate: #6d6e71;
    --slate-dark: #5f6063;
    --sky: #1eaee8;
    --sky-light: #3cc0f2;
    --ink: #6b6c6f;
    --paper: #ffffff;
    --rule: #7c7d80;
  }
  * { margin: 0; padding: 0; box-sizing: border-box; }
  html, body { width: 1200px; height: 950px; overflow: hidden; }
  body {
    background: var(--bg);
    font-family: "Arimo", Arial, sans-serif;
    position: relative;
  }
  .card {
    position: absolute;
    left: 250px;
    width: 700px;
    height: 400px;
    overflow: hidden;
    box-shadow: 0 6px 18px rgba(0,0,0,.18);
  }
  .card--back { top: 50px; background: var(--slate); }
  .card--front { top: 500px; background: var(--paper); }

  .brand { position: absolute; }
  .brand__name {
    font-family: "Montserrat", sans-serif;
    font-weight: 600;
    line-height: 1;
    letter-spacing: -1px;
  }
  .brand__sub {
    font-family: "Montserrat", sans-serif;
    font-weight: 600;
    letter-spacing: 2px;
    line-height: 1;
  }
  .brand__mark { position: absolute; }

  /* back */
  .card--back .brand { left: 120px; top: 125px; color: var(--paper); }
  .card--back .brand__mark {
    left: 0; top: 14px; width: 54px; height: 54px;
    border: 3px solid var(--paper);
  }
  .card--back .brand__name { margin-left: 76px; font-size: 66px; }
  .card--back .brand__sub { margin-left: 80px; margin-top: 4px; font-size: 24px; }
  .tagline {
    position: absolute; left: 330px; top: 265px;
    color: var(--paper); font-size: 17px;
  }

  /* front */
  .front-band { position: absolute; inset: 0; width: 700px; height: 400px; }
  .card--front .brand { left: 55px; top: 95px; color: var(--sky); }
  .card--front .brand__mark {
    left: 0; top: 12px; width: 44px; height: 44px;
    border: 2.5px solid var(--sky);
  }
  .card--front .brand__name { margin-left: 62px; font-size: 56px; }
  .card--front .brand__sub { margin-left: 64px; margin-top: 2px; font-size: 18px; }

  .contact { position: absolute; left: 155px; top: 205px; color: var(--ink); }
  .contact__name { color: var(--sky); font-weight: 700; font-size: 22px; margin-bottom: 14px; }
  .contact__address { font-size: 16px; line-height: 1.3; margin-left: 22px; margin-bottom: 10px; }
  .contact__list { list-style: none; margin-left: 22px; }
  .contact__item { display: flex; align-items: center; font-size: 16px; height: 24px; }
  .contact__icon { width: 17px; height: 17px; margin-right: 14px; margin-left: -30px; }
</style>
</head>
<body>

<section class="card card--back" aria-label="Card back">
  <div class="brand">
    <span class="brand__mark"></span>
    <div class="brand__name">quillbrook</div>
    <div class="brand__sub">NETWORKS LTD.</div>
  </div>
  <p class="tagline">Revolutionizing IT Services</p>
</section>

<section class="card card--front" aria-label="Card front">
  <svg class="front-band" viewBox="0 0 700 400" aria-hidden="true">
    <defs>
      <linearGradient id="skyFade" x1="0" y1="0" x2="1" y2="1">
        <stop offset="0" stop-color="var(--sky)"/>
        <stop offset="1" stop-color="var(--sky-light)"/>
      </linearGradient>
    </defs>
    <polygon points="452,0 700,0 700,400 612,400 570,100" fill="url(#skyFade)"/>
    <polyline points="436,0 556,104 598,400" fill="none" stroke="var(--rule)" stroke-width="7"/>
  </svg>

  <div class="brand">
    <span class="brand__mark"></span>
    <div class="brand__name">quillbrook</div>
    <div class="brand__sub">NETWORKS LTD.</div>
  </div>

  <div class="contact">
    <p class="contact__name">Maren Holt</p>
    <p class="contact__address">2170 Alder Crescent<br>Vancouver, BC V6K 1P4</p>
    <ul class="contact__list">
      <li class="contact__item">
        <svg class="contact__icon" viewBox="0 0 20 20" aria-hidden="true"><circle cx="10" cy="10" r="10" fill="var(--sky)"/><path d="M6 5.5h2.5l1 3-1.5 1a6 6 0 0 0 2.5 2.5l1-1.5 3 1V14a1.5 1.5 0 0 1-1.5 1.5A9 9 0 0 1 4.5 7 1.5 1.5 0 0 1 6 5.5z" fill="#fff"/></svg>
        604 555 0148
      </li>
      <li class="contact__item">
        <svg class="contact__icon" viewBox="0 0 20 20" aria-hidden="true"><circle cx="10" cy="10" r="10" fill="var(--sky)"/><rect x="5" y="6.5" width="10" height="7" fill="#fff"/><path d="M5 6.5l5 4 5-4" fill="none" stroke="var(--sky)" stroke-width="1.2"/></svg>
        maren@quillbrook.me
      </li>
      <li class="contact__item">
        <svg class="contact__icon" viewBox="0 0 20 20" aria-hidden="true"><circle cx="10" cy="10" r="10" fill="var(--sky)"/><circle cx="10" cy="10" r="5" fill="none" stroke="#fff" stroke-width="1.4"/><path d="M5 10h10M10 5c-2.5 3-2.5 7 0 10M10 5c2.5 3 2.5 7 0 10" fill="none" stroke="#fff" stroke-width="1"/></svg>
        www.quillbrook.me
      </li>
    </ul>
  </div>
</section>

</body>
</html>
```